Grain Roll Package Re-Design (Food)

Attached is our current package design. We need complete re-design of our current package. Here are changes needed:

1) Product name:
Product name doesn't catch consumer's eyes. Product name itself must stand out. By looking at the product name, consumer must get an idea of what this product is.
Also, product name needs to be changed to 'Baked 21 Grain Cheese Bites'.

Also the main feature of this product is that it is made of 21 Multi Grains. So this must be reflected clearly on the package! Without reading the package, consumer must clearly understand that this product is made of 21 Multi Grains therefore, it is a healthy snack, great replacement for meals.

2) Product actual size picture:
On the front side of the package, there must be an actual size of the product.

3) Net Weight
Needs to be 2.82 oz (80g)

4) Velto logo needs to be changed to the new uploaded one (with grandma face).

5) Dorquin, Inc logo attached (Manufactured exclusively for Dorquin, Inc.)

6) Example package we liked were
www.plivosnacks.example (simple but powerful, clean and clearly tells what the product is)
www.torbilfare.example
Merla Voss's food
Fenwo Crunch Wafers

Current package AI file is on the following dropbox:

https://www.filevaultly.example/sh/kqrw48ytnbzdmvx/QXLmTrUoWa_PlVcNkEsdTy7b?dl=0

Actual Product Image:
I've uploaded on my product page.

Our current package design needs to be completely changed into new design.
Updates

Hi I've uploaded both AI and PDF files of product actual image. Please put the actual product image. You don't have to put the exact same image (whether you put one roll image or whole group, I will leave up to the designer. Be creative!). Thanks.

Thank you for your participation in our project. Due to the production issue, we will need only one flavor (Cheese). We reviewed all of designs you have submitted and we felt there were many great designs. However, we felt none of design has reflected the feature of 21 grain. The main essential feature of this product is that it is made of 21 Multi Grains, and this point should be emphasized. This is the main feature that differentiates our product from others. This product is a healthy snack, and it can be a great meal replacement since it is made of 21 multi grains.

I will need only one design (I won't need Green Tea, Strawberry, Chocolate flavors). So I will need one design for one product (Baked 21 Grain Cheese Bites). I showed all of your design drafts to my buyers. Buyers have commented that the none of the packages reflect or show that this product is made of 21 kind of multi grains. This is the very crucial important factor. I need a design that shows the product is made of multi grains so healthy snack. You can use my old existing design I've uploaded.

Target Market(s)

Mothers, LOHAS consumers, Millenials, Foodies

Industry/Entity Type

Food Production

Requirements
Must have
• 21 Multi Grain must be clearly and strongly emphasized on the package. This product is a special, healthy and unique snack because it is made of 21 kinds of Multi Grains!
Nice to have
• COLORFUL, CONSISTENCY
• I'VE UPLOADED THE OTHER COMPANIES' PACKAGES I LIKED
• http://www.trandelpantry.example/products

```html
<!DOCTYPE html>
<html lang="en">
<head>
<meta charset="UTF-8">
<title>Velto Baked 21 Grain Cheese Bites – Colour Variants</title>
<link rel="stylesheet" href="https://fonts.googleapis.com/css2?family=Lora:wght@400;700&family=Lobster&display=swap">
<style>
  :root {
    --page: #ffffff;
    --kraft: #e8d2a0;
    --bite-light: #e2b877;
    --bite-mid: #cf9a55;
    --bite-dark: #b47a3c;
    --yellow: #fff157;
    --red: #dc2531;
    --green: #627f30;
    --brown: #8a2c10;
    --ink-black: #111111;
    --brand: #8e1f1c;
    --grain-1: #c98a3e;
    --grain-2: #7a4a22;
    --grain-3: #e9c46a;
    --grain-4: #5b3a1e;
    --grain-5: #f2e2b8;
  }
  * { margin: 0; padding: 0; box-sizing: border-box; }
  html, body {
    width: 1200px; height: 1200px; overflow: hidden;
    background: var(--page);
  }
  .canvas { position: relative; width: 1200px; height: 1200px; }

  .pack {
    position: absolute;
    width: 338px; height: 547px;
    background: var(--kraft);
    overflow: hidden;
  }
  .pack--yellow { left: 237px; top: 46px;  --band: var(--yellow); --ink: var(--ink-black); --band-ink: var(--ink-black); }
  .pack--red    { left: 653px; top: 48px;  --band: var(--red);    --ink: var(--red);       --band-ink: var(--kraft); }
  .pack--green  { left: 242px; top: 622px; --band: var(--green);  --ink: var(--green);     --band-ink: var(--kraft); }
  .pack--brown  { left: 653px; top: 622px; --band: var(--brown);  --ink: var(--brown);     --band-ink: var(--kraft); }

  .pack__band {
    position: absolute; left: 0; top: 0;
    width: 100%; height: 122px;
    background: var(--band);
  }

  .pack__grains {
    position: absolute; left: 0; top: 22px; width: 100%;
    text-align: center; color: var(--band-ink);
  }
  .pack__grains-label {
    display: block;
    font-family: "Lora", serif; font-weight: 700;
    font-size: 12px; letter-spacing: 3px; line-height: 16px;
  }
  .pack__grains-row {
    display: block; margin: 10px auto 0; width: 252px; height: 12px;
  }

  .pack__brand {
    position: absolute; left: 50%; top: 120px;
    transform: translate(-50%, -50%);
    display: flex; align-items: center; gap: 8px;
    padding: 6px 18px;
    background: var(--kraft);
    border-radius: 40px;
  }
  .pack__brand-dot {
    width: 12px; height: 12px; border-radius: 50%;
    background: var(--brand);
  }
  .pack__brand-name {
    font-family: "Lora", serif; font-weight: 700;
    font-size: 30px; line-height: 1;
    color: var(--brand);
  }

  .pack__photo {
    position: absolute; left: 22px; top: 262px;
    width: 306px; height: 244px;
    border-radius: 46% 42% 40% 44%;
    background: radial-gradient(ellipse at 55% 50%, var(--bite-light) 0%, var(--bite-mid) 55%, rgba(207,154,85,0) 78%);
  }
  .pack__photo-single {
    position: absolute; left: 226px; top: 254px;
    width: 44px; height: 40px; border-radius: 10px;
    background: linear-gradient(160deg, var(--bite-light), var(--bite-dark));
  }

  .pack__title { color: var(--ink); font-weight: 400; }
  .pack__kicker,
  .pack__count,
  .pack__grain,
  .pack__flavour { position: absolute; left: 34px; display: block; white-space: nowrap; }
  .pack__kicker {
    top: 178px;
    font-family: "Lora", serif; font-weight: 400; font-size: 13px;
    letter-spacing: 4px; line-height: 16px;
  }
  .pack__count,
  .pack__grain {
    font-family: "Lobster", cursive; font-weight: 400; font-size: 40px;
    line-height: 46px;
  }
  .pack__count { top: 206px; }
  .pack__grain { top: 258px; }
  .pack__flavour {
    top: 334px;
    font-family: "Lora", serif; font-weight: 400; font-size: 29px;
    letter-spacing: 6px; line-height: 38px;
  }

  .pack__footer {
    position: absolute; left: 16px; right: 16px; bottom: 12px;
    display: flex; justify-content: space-between; align-items: baseline;
    font-family: "Lora", serif; font-size: 11px; line-height: 14px;
    color: var(--ink);
  }
  .pack__net { font-weight: 700; letter-spacing: 1px; }
  .pack__maker { font-weight: 400; }
</style>
</head>
<body>
<main class="canvas">

  <svg width="0" height="0" style="position:absolute" aria-hidden="true">
    <defs>
      <g id="grain-row">
        <circle cx="6" cy="6" r="5" fill="var(--grain-1)"/>
        <circle cx="18" cy="6" r="5" fill="var(--grain-2)"/>
        <circle cx="30" cy="6" r="5" fill="var(--grain-3)"/>
        <circle cx="42" cy="6" r="5" fill="var(--grain-4)"/>
        <circle cx="54" cy="6" r="5" fill="var(--grain-5)"/>
        <circle cx="66" cy="6" r="5" fill="var(--grain-1)"/>
        <circle cx="78" cy="6" r="5" fill="var(--grain-2)"/>
        <circle cx="90" cy="6" r="5" fill="var(--grain-3)"/>
        <circle cx="102" cy="6" r="5" fill="var(--grain-4)"/>
        <circle cx="114" cy="6" r="5" fill="var(--grain-5)"/>
        <circle cx="126" cy="6" r="5" fill="var(--grain-1)"/>
        <circle cx="138" cy="6" r="5" fill="var(--grain-2)"/>
        <circle cx="150" cy="6" r="5" fill="var(--grain-3)"/>
        <circle cx="162" cy="6" r="5" fill="var(--grain-4)"/>
        <circle cx="174" cy="6" r="5" fill="var(--grain-5)"/>
        <circle cx="186" cy="6" r="5" fill="var(--grain-1)"/>
        <circle cx="198" cy="6" r="5" fill="var(--grain-2)"/>
        <circle cx="210" cy="6" r="5" fill="var(--grain-3)"/>
        <circle cx="222" cy="6" r="5" fill="var(--grain-4)"/>
        <circle cx="234" cy="6" r="5" fill="var(--grain-5)"/>
        <circle cx="246" cy="6" r="5" fill="var(--grain-1)"/>
      </g>
    </defs>
  </svg>

  <section class="pack pack--yellow">
    <div class="pack__band"></div>
    <div class="pack__grains">
      <span class="pack__grains-label">MADE WITH 21 MULTI GRAINS</span>
      <svg class="pack__grains-row" viewBox="0 0 252 12" aria-label="21 grains"><use href="#grain-row"/></svg>
    </div>
    <div class="pack__photo" role="img" aria-label="Photo of a heap of baked grain cheese bites"></div>
    <div class="pack__photo-single" role="img" aria-label="Actual size photo of a single grain cheese bite"></div>
    <div class="pack__brand"><span class="pack__brand-dot"></span><span class="pack__brand-name">Velto</span></div>
    <h2 class="pack__title">
      <span class="pack__kicker">BAKED</span>
      <span class="pack__count">21</span>
      <span class="pack__grain">Grain</span>
      <span class="pack__flavour">CHEESE<br>BITES</span>
    </h2>
    <footer class="pack__footer">
      <span class="pack__net">NET WT 2.82 OZ (80g)</span>
      <span class="pack__maker">Made for Dorquin, Inc.</span>
    </footer>
  </section>

  <section class="pack pack--red">
    <div class="pack__band"></div>
    <div class="pack__grains">
      <span class="pack__grains-label">MADE WITH 21 MULTI GRAINS</span>
      <svg class="pack__grains-row" viewBox="0 0 252 12" aria-label="21 grains"><use href="#grain-row"/></svg>
    </div>
    <div class="pack__photo" role="img" aria-label="Photo of a heap of baked grain cheese bites"></div>
    <div class="pack__photo-single" role="img" aria-label="Actual size photo of a single grain cheese bite"></div>
    <div class="pack__brand"><span class="pack__brand-dot"></span><span class="pack__brand-name">Velto</span></div>
    <h2 class="pack__title">
      <span class="pack__kicker">BAKED</span>
      <span class="pack__count">21</span>
      <span class="pack__grain">Grain</span>
      <span class="pack__flavour">CHEESE<br>BITES</span>
    </h2>
    <footer class="pack__footer">
      <span class="pack__net">NET WT 2.82 OZ (80g)</span>
      <span class="pack__maker">Made for Dorquin, Inc.</span>
    </footer>
  </section>

  <section class="pack pack--green">
    <div class="pack__band"></div>
    <div class="pack__grains">
      <span class="pack__grains-label">MADE WITH 21 MULTI GRAINS</span>
      <svg class="pack__grains-row" viewBox="0 0 252 12" aria-label="21 grains"><use href="#grain-row"/></svg>
    </div>
    <div class="pack__photo" role="img" aria-label="Photo of a heap of baked grain cheese bites"></div>
    <div class="pack__photo-single" role="img" aria-label="Actual size photo of a single grain cheese bite"></div>
    <div class="pack__brand"><span class="pack__brand-dot"></span><span class="pack__brand-name">Velto</span></div>
    <h2 class="pack__title">
      <span class="pack__kicker">BAKED</span>
      <span class="pack__count">21</span>
      <span class="pack__grain">Grain</span>
      <span class="pack__flavour">CHEESE<br>BITES</span>
    </h2>
    <footer class="pack__footer">
      <span class="pack__net">NET WT 2.82 OZ (80g)</span>
      <span class="pack__maker">Made for Dorquin, Inc.</span>
    </footer>
  </section>

  <section class="pack pack--brown">
    <div class="pack__band"></div>
    <div class="pack__grains">
      <span class="pack__grains-label">MADE WITH 21 MULTI GRAINS</span>
      <svg class="pack__grains-row" viewBox="0 0 252 12" aria-label="21 grains"><use href="#grain-row"/></svg>
    </div>
    <div class="pack__photo" role="img" aria-label="Photo of a heap of baked grain cheese bites"></div>
    <div class="pack__photo-single" role="img" aria-label="Actual size photo of a single grain cheese bite"></div>
    <div class="pack__brand"><span class="pack__brand-dot"></span><span class="pack__brand-name">Velto</span></div>
    <h2 class="pack__title">
      <span class="pack__kicker">BAKED</span>
      <span class="pack__count">21</span>
      <span class="pack__grain">Grain</span>
      <span class="pack__flavour">CHEESE<br>BITES</span>
    </h2>
    <footer class="pack__footer">
      <span class="pack__net">NET WT 2.82 OZ (80g)</span>
      <span class="pack__maker">Made for Dorquin, Inc.</span>
    </footer>
  </section>

</main>
</body>
</html>
```